Refresh of far from plain IT company website

Our web site is starting to show it's age. You can see the existing site here: www.plumbwick.net. As a growing company we want to come across as a dynamic collection of IT experts.

We want to update the design so are open to any colour palette and look, but want to retain our current table logo. We use the logo on our business cards but with a white background - see the attached file, so you don't need to keep the brown or the green.

The design should consider the range of browsers that will be looking at the site - so please show how it will look on a wide screen laptop and a 768x1024 tablet.

We want to add some pages about our team and their skills, probably with photos of each person on the team.

This is an uncoded project - the PSD files of the design is required, not coding.
Updates

Thanks everyone for the submissions so far.  It's a holiday day in the UK today but we will get some feedback on the designs so far out to you.

Target Market(s)

Architects and other creative types looking for IT support

Industry/Entity Type

Business

Font styles to use
Serif
Sans Serif

Requirements
Must have
• Must look good on a laptop and an iPad.

```html
<!DOCTYPE html>
<html lang="en">
<head>
<meta charset="utf-8">
<title>Plumbwick – IT Support</title>
<link rel="stylesheet" href="https://fonts.googleapis.com/css2?family=Ubuntu:wght@400;500;700&family=Arimo:wght@400;700&display=swap">
<style>
:root{
  --plum:#930a52;
  --plum-dark:#7a0743;
  --gold:#d9ad00;
  --gold-light:#f2c80f;
  --ink:#222;
  --text:#333;
  --grey-rule:#cfcfcf;
  --footer:#333333;
  --footer-deep:#2b2b2b;
  --footer-text:#d8d8d8;
  --white:#fff;
}
*{box-sizing:border-box;margin:0;padding:0}
html,body{width:1200px;height:1170px;overflow:hidden;background:var(--white)}
body{position:relative;font-family:"Arimo",Arial,sans-serif;color:var(--text)}
.abs{position:absolute}

/* header */
.top-line{left:0;top:0;width:1200px;height:3px;background:var(--plum)}
.brand{left:179px;top:54px;display:flex;align-items:center;gap:14px}
.brand-mark{width:40px;height:40px;background:var(--gold)}
.brand-name{font-family:"Ubuntu",sans-serif;font-size:42px;font-weight:400;color:var(--plum);letter-spacing:.5px}
.chat-badge{left:858px;top:41px;width:165px;height:62px;background:linear-gradient(#f5d22a,var(--gold));border:1px solid #e8c200;overflow:hidden}
.chat-title{left:8px;top:8px;font-family:"Ubuntu",sans-serif;font-weight:700;font-style:italic;font-size:19px;color:var(--white)}
.chat-sub{left:6px;top:42px;font-size:8px;font-style:italic;color:#333}
.chat-person{right:0;top:0;width:60px;height:62px;background:linear-gradient(135deg,#e8c9ae,#6b4a36)}
.call-us{right:176px;top:110px;font-family:"Ubuntu",sans-serif;font-size:16px;color:var(--plum)}
.call-us b{font-weight:500}

/* nav */
.main-nav{left:0;top:134px;width:1200px;height:37px;background:var(--plum)}
.main-nav ul{list-style:none;position:absolute;left:176px;width:848px;top:0;height:37px;display:flex;justify-content:space-between;align-items:center}
.main-nav li{font-family:"Ubuntu",sans-serif;font-size:13px;font-weight:500;color:var(--white);letter-spacing:.2px}
.main-nav li.current{color:#e79cc2;font-weight:400}
.main-nav li.sep{font-size:9px}

/* hero */
.hero{left:0;top:171px;width:1200px;height:300px;background:radial-gradient(ellipse at 60% 55%,#d9d9d9 0%,#9aa0a8 40%,#434b57 100%);border-bottom:2px solid #999}
.slider-dots{left:175px;top:445px;display:flex;gap:8px}
.slider-dots span{width:10px;height:10px;background:var(--white)}
.slider-dots span:first-child{opacity:.6}
.quick-contact{left:820px;top:189px;width:205px;height:253px;background:var(--gold);border:2px solid #e8e8e8;border-radius:4px;overflow:hidden}
.quick-contact h2{height:33px;background:#333;color:var(--white);font-family:"Ubuntu",sans-serif;font-weight:500;font-size:16px;letter-spacing:.5px;text-align:center;line-height:35px}
.qc-field{position:absolute;left:14px;width:175px;height:23px;background:var(--white);font-size:10.5px;color:#999;padding:6px 7px;border-radius:2px}
.qc-submit{position:absolute;right:14px;top:218px;width:64px;height:22px;background:#2e2e2e;color:var(--white);font-family:"Ubuntu",sans-serif;font-weight:500;font-size:10.5px;text-align:center;line-height:22px;border-radius:2px}

/* services */
.section-title{font-family:"Ubuntu",sans-serif;font-weight:500;color:var(--plum)}
.services-title{left:194px;top:491px;font-size:21px}
.btn-gold{left:948px;top:490px;width:61px;height:22px;background:var(--gold);color:var(--white);font-family:"Ubuntu",sans-serif;font-weight:500;font-size:11px;text-align:center;line-height:22px;border-radius:2px}
.rule{height:2px;background:var(--grey-rule);left:159px;width:884px}
.arrow-btn{top:647px;width:22px;height:22px;background:#c6c6c6}
.card{top:561px;width:141px;height:198px;background:var(--gold);border-radius:4px;overflow:hidden;text-align:center}
.card-photo{height:129px}
.card h3{font-family:"Ubuntu",sans-serif;font-weight:500;font-size:11px;color:var(--ink);margin-top:9px}
.card p{font-size:9.5px;line-height:12px;color:#222;padding:0 8px;margin-top:1px}
.card .more{font-family:"Ubuntu",sans-serif;font-weight:500;font-size:10px;color:var(--ink);margin-top:6px}

/* welcome & news */
.welcome-title{left:175px;top:797px;font-size:21px;font-family:"Arimo",sans-serif;font-weight:400;color:#9a0b1d}
.welcome-text{left:175px;top:826px;width:597px;font-size:11.2px;line-height:17px;color:#333}
.read-more{font-family:"Ubuntu",sans-serif;font-weight:500;font-size:10.5px;color:var(--ink)}
.news-title{left:793px;top:799px;font-size:21px;font-family:"Arimo",sans-serif;color:#9a0b1d}
.news-item{left:793px;width:220px;display:flex;gap:7px}
.news-date{width:27px;height:29px;border:1px solid #555;border-radius:2px;text-align:center;flex:none;overflow:hidden}
.news-date .d{background:#555;color:var(--white);font-size:11px;height:15px;line-height:15px}
.news-date .m{font-size:8.5px;color:#333;line-height:13px;font-weight:700}
.news-item p{font-size:10.8px;line-height:13px;color:#555}

/* footer */
.site-footer{left:0;top:930px;width:1200px;height:210px;background:var(--footer)}
.footer-head{top:943px;font-family:"Ubuntu",sans-serif;font-weight:500;font-size:13px;color:#e3e3e3;letter-spacing:.4px}
.footer-rule{left:159px;top:966px;width:884px;height:1px;background:#4a4a4a}
.quick-links{left:176px;top:984px;list-style:none}
.quick-links li{font-family:"Ubuntu",sans-serif;font-weight:500;font-size:11px;color:var(--footer-text);line-height:18.5px}
.footer-text{font-size:12px;line-height:16px;color:var(--footer-text);letter-spacing:.3px}
.email-field{left:303px;top:1070px;width:156px;height:23px;background:var(--white);border-radius:2px;font-size:11px;color:#999;padding:5px 4px}
.btn-plum{left:303px;top:1103px;width:71px;height:23px;background:var(--plum);color:var(--white);font-family:"Ubuntu",sans-serif;font-weight:500;font-size:13px;text-align:center;line-height:23px;border-radius:2px}
.map{left:539px;top:1023px;width:113px;height:88px;border:2px solid var(--white);background:linear-gradient(135deg,#e4e1da,#cfd8c8)}
.contact-line{left:669px;display:flex;gap:11px;align-items:flex-start;font-size:11.5px;line-height:14px;color:var(--footer-text)}
.contact-line svg{flex:none}
.footer-brand{left:841px;top:1020px;display:flex;align-items:center;gap:10px}
.footer-brand .brand-mark{width:26px;height:26px}
.footer-brand .brand-name{font-size:34px}
.copyright{left:0;top:1139px;width:1200px;height:31px;background:var(--footer-deep);border-top:1px solid #444;text-align:center;font-size:9.5px;line-height:30px;color:#ddd}
</style>
</head>
<body>

<header>
  <div class="abs top-line"></div>
  <div class="abs brand"><span class="brand-mark"></span><span class="brand-name">plumbwick</span></div>
  <div class="abs chat-badge">
    <div class="abs chat-person" role="img" aria-label="Photo of a support agent wearing a headset"></div>
    <span class="abs chat-title">Live Chat</span>
    <span class="abs chat-sub">Click to chat with us now!</span>
  </div>
  <div class="abs call-us">CALL US: <b>020 7946 0321</b></div>
</header>

<nav class="abs main-nav">
  <ul>
    <li class="current">HOME</li><li class="sep">•</li>
    <li>ABOUT US</li><li class="sep">•</li>
    <li>WHAT WE DO</li><li class="sep">•</li>
    <li>NEWS BLOG</li><li class="sep">•</li>
    <li>ARTICLES</li><li class="sep">•</li>
    <li>CLIENTS</li><li class="sep">•</li>
    <li>PARTNERS</li><li class="sep">•</li>
    <li>CONTACT US</li>
  </ul>
</nav>

<section class="abs hero" role="img" aria-label="Hand touching a world map overlaid with glowing network connection lines"></section>
<div class="abs slider-dots"><span></span><span></span><span></span></div>

<form class="abs quick-contact">
  <h2>QUICK CONTACT</h2>
  <div class="qc-field" style="top:46px">Name</div>
  <div class="qc-field" style="top:75px">Email</div>
  <div class="qc-field" style="top:104px">Phone</div>
  <div class="qc-field" style="top:132px;height:79px">Message</div>
  <div class="qc-submit">SUBMIT</div>
</form>

<main>
  <h2 class="abs section-title services-title">Our Services</h2>
  <div class="abs btn-gold">VIEW ALL</div>
  <div class="abs rule" style="top:531px"></div>

  <div class="abs arrow-btn" style="left:160px"><svg width="22" height="22"><path d="M13 6 L8 11 L13 16" fill="none" stroke="#555" stroke-width="2"/></svg></div>
  <div class="abs arrow-btn" style="left:1021px"><svg width="22" height="22"><path d="M9 6 L14 11 L9 16" fill="none" stroke="#555" stroke-width="2"/></svg></div>

  <article class="abs card" style="left:195px">
    <div class="card-photo" role="img" aria-label="Team of colleagues joining hands in a circle" style="background:linear-gradient(160deg,#d9d9dc,#4a4a55)"></div>
    <h3>IT Support &amp; Management</h3>
    <p>Lorem ipsum djnsdolor sit amet, consectetuer</p>
    <div class="more">READ MORE</div>
  </article>
  <article class="abs card" style="left:362px">
    <div class="card-photo" role="img" aria-label="Glowing cloud computing icon connected to devices" style="background:radial-gradient(circle at 50% 40%,#48c2f0,#0b3a66 75%)"></div>
    <h3>Cloud Computing</h3>
    <p>Lorem ipsum djnsdolor sit amet, consectetuer</p>
    <div class="more">READ MORE</div>
  </article>
  <article class="abs card" style="left:530px">
    <div class="card-photo" role="img" aria-label="Stressed office worker at a computer with a falling chart" style="background:linear-gradient(135deg,#cfe6f4,#8fb9d6)"></div>
    <h3>Disaster Recovery</h3>
    <p>Lorem ipsum djnsdolor sit amet, consectetuer</p>
    <div class="more">READ MORE</div>
  </article>
  <article class="abs card" style="left:697px">
    <div class="card-photo" role="img" aria-label="Hand touching a glowing server interface" style="background:linear-gradient(135deg,#6d9ccc,#12325c)"></div>
    <h3>Virtualisation</h3>
    <p>Lorem ipsum djnsdolor sit amet, consectetuer</p>
    <div class="more">READ MORE</div>
  </article>
  <article class="abs card" style="left:864px">
    <div class="card-photo" role="img" aria-label="Businessman facing a wall of sketched diagrams" style="background:linear-gradient(160deg,#e3e3e3,#7c7c7c)"></div>
    <h3>CAD Services</h3>
    <p>Lorem ipsum djnsdolor sit amet, consectetuer</p>
    <div class="more">READ MORE</div>
  </article>

  <div class="abs rule" style="top:781px;height:1px"></div>

  <h2 class="abs welcome-title">Welcome to Plumbwick</h2>
  <p class="abs welcome-text">Lorem ipsum dolor sit amet, consectetuer adipiscing elit, sed diam nonummy nibh euismod tincidunt ut laoreet dolore magna aliquam erat volutpat. Ut wisi enim ad minim veniam, quis nostrud exerci tation ullamcorper suscipit lobortis nisl ut aliquip ex ea commodo consequat. Duis autem vel eum iriure dolor in hendrerit in vulputate velit esse molestie consequat, vel illum dolore eu feugiat nulla facilisis at vero eros et accumsan et iusto odio dignissim qui blandit.</p>
  <span class="abs read-more" style="left:706px;top:898px">READ MORE</span>

  <h2 class="abs news-title">News</h2>
  <div class="abs news-item" style="top:830px">
    <div class="news-date"><div class="d">17</div><div class="m">APR</div></div>
    <p>Excepteur sint occaecat cooid ent, su ntin culpa qui officia deserunt.</p>
  </div>
  <div class="abs news-item" style="top:867px">
    <div class="news-date"><div class="d">16</div><div class="m">APR</div></div>
    <p>Excepteur sint occaecat cooid ent, su ntin culpa qui officia deserunt.</p>
  </div>
  <span class="abs read-more" style="left:947px;top:898px">READ MORE</span>
</main>

<footer>
  <div class="abs site-footer"></div>
  <h3 class="abs footer-head" style="left:177px">QUICK LINKS</h3>
  <h3 class="abs footer-head" style="left:302px">NEWS LETTER</h3>
  <h3 class="abs footer-head" style="left:537px">CONTACT INFO</h3>
  <div class="abs footer-rule"></div>

  <ul class="abs quick-links">
    <li>HOME</li><li>ABOUT US</li><li>WHAT WE DO</li><li>NEWS BLOG</li>
    <li>ARTICLES</li><li>CLIENTS</li><li>PARTNERS</li><li>CONTACT US</li>
  </ul>

  <p class="abs footer-text" style="left:305px;top:985px;width:195px">Lorem ipsum minim veniam, quis nostrud exerci tation ullamcorper suscipit. Duis autem vel eum iriure dolor in hendrerit in vulputate velit esse mole.</p>
  <div class="abs email-field">Enter your email address</div>
  <div class="abs btn-plum">SUBMIT</div>

  <p class="abs footer-text" style="left:539px;top:986px;width:290px">Lorem ipsum minim veniam, quis nostrud exerci tation ullamcorper suscipit.</p>
  <div class="abs map" role="img" aria-label="Street map showing the office location"></div>

  <div class="abs contact-line" style="top:1019px">
    <svg width="12" height="16" viewBox="0 0 12 16"><path d="M6 0a6 6 0 0 0-6 6c0 4 6 10 6 10s6-6 6-10a6 6 0 0 0-6-6zm0 8.5A2.5 2.5 0 1 1 6 3.5a2.5 2.5 0 0 1 0 5z" fill="#cfcfcf"/></svg>
    <span style="margin-left:4px">Larch House<br>48-52 Mill Lane<br>London EC2A 4QT<br>United Kingdom</span>
  </div>
  <div class="abs contact-line" style="top:1080px">
    <svg width="15" height="15" viewBox="0 0 15 15"><circle cx="7.5" cy="7.5" r="6.5" fill="none" stroke="#cfcfcf" stroke-width="1.3"/><path d="M5 4.5l1.2 1.6-.7.9c.5 1 1.2 1.7 2.2 2.2l.9-.7 1.6 1.2-.7 1.2C7 10.6 4.6 8 4.3 5.3z" fill="#cfcfcf"/></svg>
    <span>020 7946 0321</span>
  </div>
  <div class="abs contact-line" style="top:1101px">
    <svg width="15" height="11" viewBox="0 0 15 11"><rect x=".5" y=".5" width="14" height="10" fill="none" stroke="#cfcfcf"/><path d="M.5 .5l7 5 7-5" fill="none" stroke="#cfcfcf"/></svg>
    <span>website@plumbwick.net</span>
  </div>

  <div class="abs footer-brand"><span class="brand-mark"></span><span class="brand-name">plumbwick</span></div>

  <div class="abs copyright">COPYRIGHT 2014 | PLUMBWICK | ALL RIGHTS RSERVED.</div>
</footer>

</body>
</html>
```